Stationery Set for Velmora Company

I need to create full stationery design for my company; Business Cards, Envelops, Letter Heads, Calendar.
In the letter head and Envelops... only contact information and website links.
Our company is a Service Management company with different domains of innovative services including Technology Service Management, Education Services, Outsourcing Management, Events Management.
I need a modern and innovative design specially for the business card. I some transparent designs and I like it, but don't limit your innovation to what I mentioned. Sky is limit for your innovation.

Target Market(s)

Middle East & Africa

Industry/Entity Type

Business Management

Colors
34a7d8
0355a3
85acd3
86cae7
cee9f5
cfdeed
e4daeb
f3f1f8
ecf7fb

Requirements
Must have
• Name, Title, Email, Mobile
Nice to have
• We have multiple locations in USA, KSA, EGY, so I need ideas about how to include all contact details maybe QR / Barcode or something else.
• Please see our locations and contact information: www.brightvelmora.example
Should not have
• Too much text

```html
<!DOCTYPE html>
<html lang="en">
<head>
<meta charset="UTF-8">
<title>Velmora Company – Business Card</title>
<link rel="stylesheet" href="https://fonts.googleapis.com/css2?family=Fira+Sans:wght@400;500;600&display=swap">
<style>
  :root {
    --backdrop: #8f9192;
    --card: #f2f2f4;
    --ink: #1d1d22;
    --brand-blue: #2f5ea8;
    --band-grey: #b9b4b7;
    --pattern-tone: #dde3ee;
    --pattern-soft: #eceff5;
  }
  * { margin: 0; padding: 0; box-sizing: border-box; }
  html, body {
    width: 1105px; height: 1200px; overflow: hidden;
    background: var(--backdrop);
    font-family: "Fira Sans", Arial, sans-serif;
    color: var(--ink);
  }
  .stage { position: relative; width: 1105px; height: 1200px; }
  .card {
    position: absolute; left: 182px; width: 747px; height: 425px;
    background: var(--card); overflow: hidden;
  }
  .card--front { top: 119px; }
  .card--back { top: 636px; }
  .band { position: absolute; left: 0; right: 0; height: 14px; }
  .band--top { top: 0; background: var(--band-grey); }
  .band--bottom { bottom: 0; background: var(--brand-blue); }

  .brand {
    display: flex; align-items: center; gap: 10px;
    font-weight: 600; font-size: 31px; color: var(--brand-blue);
    white-space: nowrap;
  }
  .brand__dot { width: 14px; height: 14px; border-radius: 50%; background: var(--brand-blue); }

  .card--front .brand { position: absolute; left: 88px; top: 150px; }
  .identity { position: absolute; left: 60px; width: 290px; top: 262px; text-align: center; }
  .identity__name { font-weight: 500; font-size: 24px; color: var(--brand-blue); letter-spacing: 0.5px; }
  .identity__title { font-size: 18px; margin-top: 4px; }

  .contacts { position: absolute; left: 414px; top: 54px; font-size: 18.5px; line-height: 27.5px; }
  .contacts__block + .contacts__block { margin-top: 10px; }
  .contacts__line { display: flex; align-items: center; gap: 12px; }
  .contacts__line svg { width: 17px; height: 17px; fill: var(--brand-blue); flex: none; }

  .card--back .brand { position: absolute; left: 0; right: 0; top: 80px; justify-content: center; }
  .pattern {
    position: absolute; left: 0; right: 0; top: 250px; bottom: 0;
    background: linear-gradient(180deg, var(--pattern-soft), var(--pattern-tone));
  }
</style>
</head>
<body>
<div class="stage">
  <section class="card card--front">
    <div class="band band--top"></div>
    <div class="brand"><span class="brand__dot"></span>Velmora Company</div>
    <div class="identity">
      <div class="identity__name">DANIEL HART</div>
      <div class="identity__title">CEO/Founder</div>
    </div>
    <div class="contacts">
      <div class="contacts__block">
        <div>418 Harbor Crest Lane</div>
        <div>5th Floor Marlow Bay</div>
        <div>CA 94100 US</div>
        <div class="contacts__line">
          <svg viewBox="0 0 24 24"><path d="M6.6 10.8a15.1 15.1 0 0 0 6.6 6.6l2.2-2.2c.3-.3.7-.4 1-.2 1.1.4 2.3.6 3.6.6.6 0 1 .4 1 1V20c0 .6-.4 1-1 1A17 17 0 0 1 3 4c0-.6.4-1 1-1h3.5c.6 0 1 .4 1 1 0 1.3.2 2.5.6 3.6.1.3 0 .7-.2 1z"/></svg>
          <span>+1.5550187342</span>
        </div>
      </div>
      <div class="contacts__block">
        <div>Riyadh, Al Nakheel,</div>
        <div>Qasr Al Noor St.</div>
        <div>Ranim Towers</div>
        <div>Block 3C 4th Floor C12, C14</div>
        <div class="contacts__line">
          <svg viewBox="0 0 24 24"><path d="M6.6 10.8a15.1 15.1 0 0 0 6.6 6.6l2.2-2.2c.3-.3.7-.4 1-.2 1.1.4 2.3.6 3.6.6.6 0 1 .4 1 1V20c0 .6-.4 1-1 1A17 17 0 0 1 3 4c0-.6.4-1 1-1h3.5c.6 0 1 .4 1 1 0 1.3.2 2.5.6 3.6.1.3 0 .7-.2 1z"/></svg>
          <span>+966 90000 18 37</span>
        </div>
      </div>
      <div class="contacts__block">
        <div class="contacts__line">
          <svg viewBox="0 0 24 24"><path d="M7 1h10a2 2 0 0 1 2 2v18a2 2 0 0 1-2 2H7a2 2 0 0 1-2-2V3a2 2 0 0 1 2-2zm0 3v14h10V4zm5 15.2a1.2 1.2 0 1 0 0 2.4 1.2 1.2 0 0 0 0-2.4z"/></svg>
          <span>+1.5550187342</span>
        </div>
        <div class="contacts__line">
          <svg viewBox="0 0 24 24"><path d="M2 5h20v14H2zm2 2v.4l8 5.2 8-5.2V7z"/></svg>
          <span>info@velmora.example</span>
        </div>
      </div>
    </div>
    <div class="band band--bottom"></div>
  </section>

  <section class="card card--back">
    <div class="brand"><span class="brand__dot"></span>Velmora Company</div>
    <div class="pattern" role="img" aria-label="Faint pattern of scattered outlined light bulbs in pale blue"></div>
  </section>
</div>
</body>
</html>
```